Business card design for my company.
I would like the card's background colour to be black. You can also see our web site to get an idea of our brand. https://www.tmwhomecrafting.com.au/
- Name
- Email

```html
<!DOCTYPE html>
<html lang="en">
<head>
<meta charset="utf-8">
<title>TMW Home Crafting – Business Card</title>
<link href="https://fonts.googleapis.com/css2?family=Montserrat:wght@400;500;700;800&display=swap" rel="stylesheet">
<style>
  :root{
    --stage:#2b2b2b;
    --card:#050505;
    --green:#12994a;
    --white:#f4f4f4;
    --muted:#d8d8d8;
  }
  *{box-sizing:border-box;margin:0;padding:0}
  html,body{width:1200px;height:875px;overflow:hidden}
  body{
    background:var(--stage);
    font-family:'Montserrat',sans-serif;
    position:relative;
  }
  .card{
    position:absolute;
    width:520px;height:300px;
    background:var(--card);
    border-radius:18px;
    overflow:hidden;
    box-shadow:0 20px 40px rgba(0,0,0,.45);
  }
  .card--front{left:50px;top:288px}
  .card--back{left:630px;top:288px}

  .wordmark{
    display:flex;align-items:center;gap:12px;
    color:var(--white);
    font-weight:800;
    letter-spacing:.08em;
    text-transform:uppercase;
    line-height:1;
  }
  .wordmark__square{background:var(--green);flex:none}
  .card--front .wordmark{
    position:absolute;left:50%;top:50%;transform:translate(-50%,-50%);
    font-size:30px;white-space:nowrap;
  }
  .card--front .wordmark__square{width:22px;height:22px}

  .card--back .wordmark{
    position:absolute;left:70px;top:70px;font-size:22px;
  }
  .card--back .wordmark__square{width:16px;height:16px}

  .person{position:absolute;left:70px;top:150px}
  .person__name{color:var(--green);font-weight:800;font-size:22px}
  .person__role{color:var(--white);font-weight:500;font-size:12px;margin-top:4px}

  .divider{position:absolute;left:232px;top:142px;width:2px;height:62px;background:var(--green)}

  .contact{position:absolute;left:250px;top:140px;list-style:none}
  .contact li{
    display:flex;align-items:center;gap:8px;
    color:var(--white);font-size:11.5px;font-weight:500;
    margin-bottom:7px;white-space:nowrap;
  }
  .contact svg{width:12px;height:12px;flex:none;fill:var(--green)}

  .bands{position:absolute;left:0;bottom:0;width:520px;height:300px}
</style>
</head>
<body>

<section class="card card--front" aria-label="Card front">
  <div class="wordmark"><span class="wordmark__square"></span>TMW Home Crafting</div>
</section>

<section class="card card--back" aria-label="Card back">
  <div class="wordmark"><span class="wordmark__square"></span>TMW Home Crafting</div>

  <div class="person">
    <p class="person__name">Liam Carter</p>
    <p class="person__role">Managing Director</p>
  </div>

  <span class="divider"></span>

  <ul class="contact">
    <li>
      <svg viewBox="0 0 24 24" aria-hidden="true"><path d="M6.6 10.8a15.1 15.1 0 0 0 6.6 6.6l2.2-2.2a1 1 0 0 1 1-.25 11.4 11.4 0 0 0 3.6.57 1 1 0 0 1 1 1V20a1 1 0 0 1-1 1A17 17 0 0 1 3 4a1 1 0 0 1 1-1h3.5a1 1 0 0 1 1 1c0 1.25.2 2.45.57 3.57a1 1 0 0 1-.25 1z"/></svg>
      (08) 9000 4821
    </li>
    <li>
      <svg viewBox="0 0 24 24" aria-hidden="true"><path d="M2 5h20v14H2zm2 2v.5l8 5 8-5V7l-8 5z"/></svg>
      info@tmwhomecrafting.com.au
    </li>
    <li>
      <svg viewBox="0 0 24 24" aria-hidden="true"><path d="M12 2a10 10 0 1 0 0 20 10 10 0 0 0 0-20zm6.9 9h-3a15 15 0 0 0-1.3-5.6A8 8 0 0 1 18.9 11zM12 4.1c.9 1.3 1.8 3.6 2 6.9h-4c.2-3.3 1.1-5.6 2-6.9zM9.4 5.4A15 15 0 0 0 8.1 11h-3a8 8 0 0 1 4.3-5.6zM5.1 13h3a15 15 0 0 0 1.3 5.6A8 8 0 0 1 5.1 13zm6.9 6.9c-.9-1.3-1.8-3.6-2-6.9h4c-.2 3.3-1.1 5.6-2 6.9zm2.6-1.3a15 15 0 0 0 1.3-5.6h3a8 8 0 0 1-4.3 5.6z"/></svg>
      www.tmwhomecrafting.com.au
    </li>
  </ul>

  <svg class="bands" viewBox="0 0 520 300" aria-hidden="true">
    <polygon points="0,288 362,258 350,300 0,300" fill="var(--green)"/>
    <polygon points="374,256 520,228 520,300 362,300" fill="var(--white)"/>
  </svg>
</section>

</body>
</html>
```